Etikett für Rotweinflasche
Liebe farbkosmos Atelier, wir werden uns bei der endgültigen Etikettengestaltung (finale Größe + Rückseite) noch an Euch melden. Bitte sendet uns euren Kontakt an helga.brandt@morvelli.wine
Zielgruppe
Morvelli Italia ist ein exklusives Boutique-Weingut in Sizilien, das hochqualitative Spitzenweine in kleinen Mengen mit modernster Technologie und stets nachhaltig erzeugt. Wir hinterfragen sowohl in der Agronomie im Weingarten als auch in der Önologie im Weinkeller alle herrschenden Traditionen und trachten danach, stets das beste Endprodukt zu kreieren. Der vulkanische, kalkreiche Boden Siziliens sowie trockene, sonnenreiche und niederschlagsarme Vegetationsperioden sind unsere optimale Basis.
Zielgruppe: Internationale Genussmenschen jeglichen Alters, die sich bewusst auch höherpreisige Weine (um die €30+) gönnen , vor allem kunstaffine young professionals mit Qualitäts-& Nachhaltigkeitsanspruch
Aufgabenstellung
Das Etikett ist für Rotwein-Flaschen (Cabernet Sauvignon / Nero D'Avola / Frappato / Syrah / Cerasuolo / Petit Verdot / sowie einen Bourdeaux-Cuveè aus Cabernet Sauvignon und Petit Verdot) .
Die Flasche ist reinschwarz, sehr hochwertig und schwer.
Flaschenform: Bordeauxflasche siehe technisches Datenblatt
Sleeve über dem Korken: schwarz mit weißer Schrift wie bisher
Zu gestalten ist das Etikett der Vorderseite. Zumindest die jeweilige Rotwein-Sorte ist auch textlich darzustellen (zwecks Scannen mit Trubel-App)
Der Kreativität kann freien Lauf gelassen werden! Unterscheidbarkeit vom Markt ist explizit gewollt.
Unsere aktuellen Etiketten und Markenauftritt siehe: https://morvelli.wine/shop/

```html
<!DOCTYPE html>
<html lang="de">
<head>
<meta charset="utf-8">
<title>Cabernet Sauvignon – Etikett Vorderseite</title>
<link rel="stylesheet" href="https://fonts.googleapis.com/css2?family=Oswald:wght@300&display=swap">
<style>
  :root {
    --page-bg: #ffffff;
    --band-gold: #f2c46a;
    --ink-dark: #2a1c22;
    --art-crimson: #c8213f;
    --art-magenta: #b52a6a;
    --art-violet: #5a3393;
    --art-indigo: #2e2c78;
    --art-gold: #e9b24c;
    --art-teal: #2f7f9a;
    --art-rose: #e4607c;
    --art-lilac: #c98fc4;
  }
  html, body {
    margin: 0;
    padding: 0;
    width: 849px;
    height: 1200px;
    overflow: hidden;
    background: var(--page-bg);
  }
  .front-label {
    position: absolute;
    left: 25px;
    top: 24px;
    width: 800px;
    height: 1152px;
    display: flex;
    flex-direction: column;
    overflow: hidden;
  }
  .varietal-band {
    height: 64px;
    flex: 0 0 64px;
    background: var(--band-gold);
    display: flex;
    align-items: center;
    justify-content: center;
  }
  .varietal-name {
    margin: 0;
    font-family: 'Oswald', sans-serif;
    font-weight: 300;
    font-size: 34px;
    letter-spacing: 0.38em;
    color: var(--ink-dark);
    text-transform: uppercase;
    line-height: 1;
    padding-left: 0.38em;
  }
  .owl-artwork {
    flex: 1 1 auto;
    display: block;
    width: 100%;
  }
</style>
</head>
<body>
  <main class="front-label">
    <header class="varietal-band">
      <h1 class="varietal-name">Cabernet Sauvignon</h1>
    </header>
    <svg class="owl-artwork" viewBox="0 0 800 1088" preserveAspectRatio="none"
         role="img" aria-label="Farbenfrohe Aquarell-Illustration einer Eule mit großen goldenen Augen, in Magenta, Violett, Indigo, Gold und Rosa">
      <defs>
        <linearGradient id="base-tones" x1="0" y1="0" x2="0" y2="1">
          <stop offset="0" stop-color="var(--art-magenta)"/>
          <stop offset="0.18" stop-color="var(--art-crimson)"/>
          <stop offset="0.38" stop-color="var(--art-violet)"/>
          <stop offset="0.58" stop-color="var(--art-indigo)"/>
          <stop offset="0.78" stop-color="var(--art-magenta)"/>
          <stop offset="1" stop-color="var(--art-rose)"/>
        </linearGradient>
        <linearGradient id="gold-wash" x1="0" y1="0" x2="1" y2="0">
          <stop offset="0" stop-color="var(--art-gold)" stop-opacity="0.85"/>
          <stop offset="0.35" stop-color="var(--art-gold)" stop-opacity="0.15"/>
          <stop offset="0.5" stop-color="var(--art-teal)" stop-opacity="0.35"/>
          <stop offset="0.65" stop-color="var(--art-gold)" stop-opacity="0.15"/>
          <stop offset="1" stop-color="var(--art-gold)" stop-opacity="0.85"/>
        </linearGradient>
        <linearGradient id="gold-fade" x1="0" y1="0" x2="0" y2="1">
          <stop offset="0" stop-color="#fff" stop-opacity="0"/>
          <stop offset="0.12" stop-color="#fff" stop-opacity="0.6"/>
          <stop offset="0.42" stop-color="#fff" stop-opacity="1"/>
          <stop offset="0.6" stop-color="#fff" stop-opacity="0"/>
          <stop offset="1" stop-color="#fff" stop-opacity="0"/>
        </linearGradient>
        <mask id="gold-mask">
          <rect x="0" y="0" width="800" height="1088" fill="url(#gold-fade)"/>
        </mask>
        <radialGradient id="lilac-glow" cx="0.5" cy="1" r="0.45">
          <stop offset="0" stop-color="var(--art-lilac)" stop-opacity="0.8"/>
          <stop offset="1" stop-color="var(--art-lilac)" stop-opacity="0"/>
        </radialGradient>
      </defs>
      <rect class="artwork-base" x="0" y="0" width="800" height="1088" fill="url(#base-tones)"/>
      <rect class="artwork-gold" x="0" y="0" width="800" height="1088" fill="url(#gold-wash)" mask="url(#gold-mask)"/>
      <rect class="artwork-glow" x="0" y="0" width="800" height="1088" fill="url(#lilac-glow)"/>
    </svg>
  </main>
</body>
</html>
```